Business Card Design

New business card design

Target Market(s)

Residential & Commercial Property Managers

Industry/Entity Type

Plumbing Services

Contact Information for Business Card

Name - Rowan Keddle, title - Director, Phone Number - 0431 286 517, email - rowan@tbk-plumbing.com.au, Company ABN - 73 215 904 386,

Font styles to use
Sans Serif

Colors
0054AA
0677BA
7BADD7
CADEEF
E8F1F8

```html
<!DOCTYPE html>
<html lang="en">
<head>
<meta charset="utf-8">
<title>tbk – Business Card</title>
<link href="https://fonts.googleapis.com/css2?family=Montserrat:wght@400;500;700&display=swap" rel="stylesheet">
<style>
  :root {
    --backdrop: #9a9a9a;
    --card: #ffffff;
    --accent: #2ea9e0;
    --ink: #1e2530;
    --text: #1f1f1f;
  }
  * { box-sizing: border-box; margin: 0; padding: 0; }
  html, body {
    width: 1093px; height: 1200px; overflow: hidden;
    background: var(--backdrop);
    font-family: "Montserrat", sans-serif;
    color: var(--text);
  }
  .card {
    position: absolute; left: 265px; width: 580px; height: 364px;
    background: var(--accent);
    border-radius: 22px;
  }
  .card--front { top: 225px; }
  .card--back { top: 616px; }
  .card__face {
    position: absolute; left: 6px; top: 0; right: 0; bottom: 6px;
    background: var(--card);
    border-radius: 20px;
    overflow: hidden;
  }
  .brand-name {
    position: absolute;
    font-family: "Montserrat", sans-serif;
    font-weight: 400;
    color: var(--ink);
    letter-spacing: 2px;
    line-height: 1;
  }
  .card--front .brand-name { left: 20px; top: 36px; font-size: 70px; }
  .card--back .brand-name { left: 0; right: 0; top: 112px; text-align: center; font-size: 84px; }
  .person {
    position: absolute; right: 35px; top: 40px; text-align: right;
  }
  .person__name { font-weight: 700; font-size: 21px; color: var(--ink); line-height: 1.1; }
  .person__title { font-weight: 400; font-size: 13px; margin-top: 2px; }
  .address {
    position: absolute; left: 25px; top: 177px;
    font-size: 13.5px; line-height: 16px; font-weight: 400;
  }
  .contacts {
    position: absolute; left: 25px; top: 234px; list-style: none;
    font-size: 13px;
  }
  .contacts li { display: flex; align-items: center; height: 25px; }
  .contacts svg { width: 13px; height: 13px; margin-right: 9px; fill: var(--ink); }
  .abn { position: absolute; left: 25px; top: 316px; font-size: 13px; }
  .abn strong { font-weight: 700; }
  .accent-circle {
    position: absolute; left: 386px; top: 190px;
    width: 156px; height: 156px; border-radius: 50%;
    background: var(--accent);
  }
</style>
</head>
<body>
  <section class="card card--front">
    <div class="card__face">
      <div class="brand-name">tbk</div>
      <div class="person">
        <div class="person__name">Rowan Keddle</div>
        <div class="person__title">Director</div>
      </div>
      <address class="address" style="font-style:normal">
        48 Harbour Ridge Road<br>Brookvale, NSW 2100
      </address>
      <ul class="contacts">
        <li>
          <svg viewBox="0 0 24 24" aria-hidden="true"><path d="M6.6 10.8a15.1 15.1 0 0 0 6.6 6.6l2.2-2.2a1 1 0 0 1 1-.25 11.4 11.4 0 0 0 3.6.57 1 1 0 0 1 1 1V20a1 1 0 0 1-1 1A17 17 0 0 1 3 4a1 1 0 0 1 1-1h3.5a1 1 0 0 1 1 1c0 1.25.2 2.45.57 3.57a1 1 0 0 1-.25 1z"/></svg>
          0431 286 517
        </li>
        <li>
          <svg viewBox="0 0 24 24" aria-hidden="true"><path d="M2 5h20v14H2z" /><path d="M2 5l10 8 10-8" fill="none" stroke="#fff" stroke-width="2"/></svg>
          rowan@tbk-plumbing.com.au
        </li>
        <li>
          <svg viewBox="0 0 24 24" aria-hidden="true"><circle cx="12" cy="12" r="10"/><path d="M2 12h20M12 2c3 3 3 17 0 20M12 2c-3 3-3 17 0 20" fill="none" stroke="#fff" stroke-width="1.5"/></svg>
          www.tbk-plumbing.com.au
        </li>
      </ul>
      <p class="abn"><strong>ABN</strong> - 73 215 904 386</p>
      <div class="accent-circle"></div>
    </div>
  </section>

  <section class="card card--back">
    <div class="card__face">
      <div class="brand-name">tbk</div>
    </div>
  </section>
</body>
</html>
```